Business card design needed

I would like a one sided black business card with the information provided above. Refer to my website www.brightvolleyracquets.com.au for an example of colors I have used for my site, would like to keep this consistent for my business cards also, I will upload my logo below.

I am a new small business that provides tennis customers with racquet re stringing, tennis strings and accessories.

Industry/Entity Type

Small Business

Contact Information for Business Card

Bright Volley Tennis

Owen Whitby
Managing Director

brightvolleyracquets@mailbox.example
www.brightvolleyracquets.com.au
0491 726 305

Racquet Restringing/Tennis Strings/Accessories

Requirements
Must have
• Must have my logo and card must be black

```html
<!DOCTYPE html>
<html lang="en">
<head>
<meta charset="utf-8">
<title>Bright Volley Tennis – Business Card</title>
<link rel="stylesheet" href="https://fonts.googleapis.com/css2?family=Source+Sans+3:wght@400;600;700&display=swap">
<style>
  :root {
    --backdrop: #e7e4e0;
    --card-black: #070707;
    --volley-green: #b8d432;
    --text-white: #f4f4f4;
    --rule-grey: #8a8a8a;
  }
  * { margin: 0; padding: 0; box-sizing: border-box; }
  html, body {
    width: 1200px;
    height: 750px;
    overflow: hidden;
    background: var(--backdrop);
    font-family: "Source Sans 3", Arial, sans-serif;
  }
  .business-card {
    position: absolute;
    left: 75px;
    top: 75px;
    width: 1050px;
    height: 598px;
    background: var(--card-black);
    border-radius: 42px;
    color: var(--text-white);
  }
  .brand-mark {
    position: absolute;
    left: 115px;
    top: 128px;
    display: flex;
    align-items: center;
    gap: 18px;
  }
  .brand-dot {
    width: 46px;
    height: 46px;
    border-radius: 50%;
    background: var(--volley-green);
  }
  .brand-name {
    font-size: 64px;
    font-weight: 700;
    color: var(--volley-green);
    letter-spacing: 0.5px;
    white-space: nowrap;
  }
  .divider-vertical {
    position: absolute;
    left: 141px;
    top: 357px;
    width: 1px;
    height: 215px;
    background: var(--rule-grey);
  }
  .divider-horizontal {
    position: absolute;
    left: 107px;
    top: 431px;
    width: 408px;
    height: 1px;
    background: var(--rule-grey);
  }
  .person-name {
    position: absolute;
    left: 157px;
    top: 348px;
    font-size: 32px;
    font-weight: 700;
    color: var(--volley-green);
  }
  .person-title {
    position: absolute;
    left: 157px;
    top: 388px;
    font-size: 25px;
    font-weight: 400;
  }
  .contact-list {
    position: absolute;
    left: 108px;
    top: 432px;
    list-style: none;
  }
  .contact-item {
    display: flex;
    align-items: center;
    height: 44px;
    font-size: 25px;
  }
  .contact-icon {
    width: 22px;
    height: 22px;
    margin-right: 23px;
    fill: var(--volley-green);
    flex: none;
  }
  .services-list {
    position: absolute;
    right: 47px;
    top: 425px;
    list-style: none;
    text-align: right;
  }
  .service-item {
    font-size: 32px;
    line-height: 44px;
  }
  .service-item::before {
    content: "";
    display: inline-block;
    width: 9px;
    height: 9px;
    background: var(--text-white);
    margin-right: 12px;
    vertical-align: 7px;
  }
</style>
</head>
<body>
  <div class="business-card">
    <div class="brand-mark">
      <span class="brand-dot"></span>
      <span class="brand-name">Bright Volley Tennis</span>
    </div>

    <div class="divider-vertical"></div>
    <div class="divider-horizontal"></div>

    <p class="person-name">Owen Whitby</p>
    <p class="person-title">Managing Director</p>

    <ul class="contact-list">
      <li class="contact-item">
        <svg class="contact-icon" viewBox="0 0 24 24" aria-hidden="true">
          <path d="M3 8c0-3 4-5 9-5s9 2 9 5v2h-5V8c-1-.6-2.4-1-4-1s-3 .4-4 1v2H3z"/>
          <path d="M6 12h12l2 9H4z"/>
          <circle cx="12" cy="16" r="2" fill="#070707"/>
        </svg>
        <span>0491 726 305</span>
      </li>
      <li class="contact-item">
        <svg class="contact-icon" viewBox="0 0 24 24" aria-hidden="true">
          <path d="M2 6h20v13H2z"/>
          <path d="M3 7l9 7 9-7" fill="none" stroke="#070707" stroke-width="1.6"/>
        </svg>
        <span>brightvolleyracquets@mailbox.example</span>
      </li>
      <li class="contact-item">
        <svg class="contact-icon" viewBox="0 0 24 24" aria-hidden="true">
          <circle cx="12" cy="12" r="10"/>
          <g fill="none" stroke="#070707" stroke-width="1.3">
            <ellipse cx="12" cy="12" rx="4.5" ry="10"/>
            <path d="M2 12h20M4 7h16M4 17h16"/>
          </g>
        </svg>
        <span>www.brightvolleyracquets.com.au</span>
      </li>
    </ul>

    <ul class="services-list">
      <li class="service-item">Racquet Restringing</li>
      <li class="service-item">Tennis Strings</li>
      <li class="service-item">Accessories</li>
    </ul>
  </div>
</body>
</html>
```